4D Cradle Glimpse Luxury Ultrasound Billboard

Design a HIGH-END, MODERN billboard for my private prenatal ultrasound studio, 4D Cradle Glimpse, located in Pace, Florida.
This billboard will be viewed by drivers traveling at highway speeds, so it must be extremely clean, simple, and readable within 6 seconds.
About My Business
4D Cradle Glimpse is a private prenatal ultrasound studio specializing in:
Highest technology 4D/HD Ultrasounds
Early Gender Determination
Pregnancy Confirmation
I have been serving families for nearly 10 years and is known for creating a memorable experience, not just an ultrasound appointment.
Design Style
I DO NOT want:
Flowers
Leaves
Swirls
Glitter
Hearts everywhere
Busy backgrounds
Generic maternity stock graphics
I DO want:
Modern
Luxury
Upscale
Clean
Professional
Eye-catching
Premium medical spa feel
Colors
Use colors from my logo:
LOGO Green ( or a deep green)
Black
White
Soft Gold accents
Images:
Incorporate my professional headshot in a clean, modern way, logo, and the ultrasound images
Text
Keep wording minimal.
Primary Headline ( OPEN TO IDEAS) :
EXAMPLES ( WOULD RATHER SOMETHING MORE CATCHY)
" ADVANCED IMAGING. UNFORGETTABLE MOMENTS"
"MEET YOUR BABY BEFORE BIRTH"
Under headline:
4D Ultrasound • Early Gender • Pregnancy Confirmation
Business Name:
4D Cradle Glimpse
Private Prenatal Ultrasound Studio
Phone Number:
850-471-5923
Important
This billboard must be readable in 5–6 seconds from a moving vehicle.
Less text is better.
The phone number and business name must be visible from a distance.
The design should feel like a premium brand that immediately tells expecting parents:
“This is where I go to see my baby.”
Files Provided
Official logo
Headshot
Ultrasound images
Don’t make this look like a medical office billboard.
Make it look like a luxury baby experience billboard. That’s what separates 4D Cradle Glimpse from hospitals, OB offices, and all the new studios popping up around you. The emotional connection is what gets moms to book. ❤️
Billboard Size - 10.6” x 36”

```html
<!DOCTYPE html>
<html lang="en">
<head>
<meta charset="utf-8">
<title>4D Cradle Glimpse Billboard</title>
<link rel="stylesheet" href="https://fonts.googleapis.com/css2?family=Montserrat:wght@600;700;800&family=Playfair+Display:wght@700&family=Poppins:wght@600;700&display=swap">
<style>
  :root {
    --stage: #d6d6d6;
    --green: #2b3a30;
    --ink: #25302a;
    --white: #ffffff;
    --cream: #f7f0e6;
    --gold: #d9ab4a;
    --gold-light: #f9dc98;
    --gold-deep: #b8892f;
  }
  * { margin: 0; padding: 0; box-sizing: border-box; }
  html, body { width: 1105px; height: 1200px; overflow: hidden; background: var(--stage); }
  .stage { position: relative; width: 1105px; height: 1200px; }
  .billboard {
    position: absolute; left: 32px; top: 340px;
    width: 1630px; height: 815px;
    transform: scale(0.638); transform-origin: top left;
    background: var(--green); overflow: hidden;
  }
  .portrait { position: absolute; left: 0; top: 0; width: 480px; height: 580px; }
  .brand-panel {
    position: absolute; left: 898px; top: 42px; width: 276px; height: 138px;
    background: var(--white); border: 3px solid #c9c9c9; border-radius: 16px;
    display: flex; align-items: center; justify-content: center; text-align: center;
  }
  .brand-name {
    font-family: "Poppins", sans-serif; font-weight: 600; font-size: 30px;
    line-height: 1.15; color: var(--green);
  }
  .headline { position: absolute; left: 480px; right: 30px; top: 206px; text-align: center; }
  .headline-lead {
    font-family: "Montserrat", sans-serif; font-weight: 800; font-size: 93px;
    color: var(--white); letter-spacing: 1px; line-height: 1;
  }
  .headline-gold {
    font-family: "Playfair Display", serif; font-weight: 700; font-size: 122px;
    line-height: 0.84; margin-top: 22px;
    background: linear-gradient(180deg, var(--gold-light) 0%, var(--gold) 45%, var(--gold-deep) 100%);
    -webkit-background-clip: text; background-clip: text; color: transparent;
  }
  .services {
    position: absolute; left: 0; top: 573px; width: 100%; height: 92px;
    padding-left: 91px;
    display: flex; align-items: center; gap: 34px;
    background: linear-gradient(90deg, var(--gold) 0%, var(--gold-light) 50%, var(--gold) 100%);
  }
  .service {
    display: flex; align-items: center; gap: 16px; white-space: nowrap;
    font-family: "Montserrat", sans-serif; font-weight: 700; font-size: 24px;
    color: var(--ink); letter-spacing: 0.5px;
  }
  .service svg { flex: none; }
  .divider { display: block; width: 2px; background: var(--ink); flex: none; }
  .services .divider { height: 44px; }
  .contact { position: absolute; left: 0; top: 665px; width: 100%; height: 150px; background: var(--cream); }
  .phone {
    position: absolute; left: 106px; top: 42px;
    font-family: "Poppins", sans-serif; font-weight: 700; font-size: 72px;
    letter-spacing: 2px; color: var(--ink); line-height: 1;
  }
  .contact .divider { position: absolute; left: 736px; top: 52px; height: 60px; }
  .years { position: absolute; left: 832px; top: 36px; }
  .years-lead {
    font-family: "Montserrat", sans-serif; font-weight: 700; font-size: 19px; color: var(--ink);
  }
  .years-count {
    font-family: "Poppins", sans-serif; font-weight: 700; font-size: 62px;
    line-height: 1; color: var(--gold); margin-top: 2px;
  }
  .scan { position: absolute; left: 1335px; top: 525px; width: 330px; height: 330px; }
</style>
</head>
<body>
<main class="stage">
  <section class="billboard">
    <svg class="portrait" viewBox="0 0 480 580" role="img" aria-label="Portrait of the studio owner seated beside an ultrasound machine">
      <defs>
        <linearGradient id="portraitTone" x1="0" y1="0" x2="1" y2="1">
          <stop offset="0" stop-color="#e9e6e2"/>
          <stop offset="0.45" stop-color="#d8c3a0"/>
          <stop offset="0.8" stop-color="#3e5a36"/>
          <stop offset="1" stop-color="#ecebea"/>
        </linearGradient>
      </defs>
      <path d="M0 0 H330 C425 90 470 300 455 573 H0 Z" fill="url(#portraitTone)"/>
      <path d="M330 0 C425 90 470 300 455 573" fill="none" stroke="#d9ab4a" stroke-width="5"/>
    </svg>

    <div class="brand-panel">
      <span class="brand-name">4D Cradle<br>Glimpse</span>
    </div>

    <header class="headline">
      <h1 class="headline-lead">ADVANCED IMAGING</h1>
      <p class="headline-gold">UNFORGETTABLE<br>MOMENTS</p>
    </header>

    <div class="services">
      <div class="service">
        <svg width="40" height="60" viewBox="0 0 40 60" fill="none" stroke="#25302a" stroke-width="2.5" stroke-linecap="round">
          <path d="M8 10 Q20 0 32 10"/><path d="M12 15 Q20 8 28 15"/>
          <path d="M11 20 H29 L26 38 Q20 44 14 38 Z"/>
          <path d="M20 42 V50 Q20 58 30 56"/>
        </svg>
        <span>4D ULTRASOUND</span>
      </div>
      <span class="divider"></span>
      <div class="service">
        <svg width="52" height="56" viewBox="0 0 52 56" fill="none" stroke="#25302a" stroke-width="3" stroke-linecap="round">
          <circle cx="16" cy="28" r="11"/><circle cx="28" cy="24" r="11"/>
          <path d="M16 39 V53 M10 47 H22"/><path d="M36 16 L48 4 M40 4 H48 V12"/>
        </svg>
        <span>EARLY GENDER</span>
      </div>
      <span class="divider"></span>
      <div class="service">
        <svg width="38" height="30" viewBox="0 0 38 30" fill="none" stroke="#25302a" stroke-width="6" stroke-linecap="round" stroke-linejoin="round">
          <path d="M4 15 L14 25 L34 4"/>
        </svg>
        <span>PREGNANCY CONFIRMATION</span>
      </div>
    </div>

    <div class="contact">
      <p class="phone">850-471-5923</p>
      <span class="divider"></span>
      <div class="years">
        <p class="years-lead">SERVING FAMILIES FOR NEARLY</p>
        <p class="years-count">10 YEARS</p>
      </div>
    </div>

    <svg class="scan" viewBox="0 0 330 330" role="img" aria-label="4D ultrasound image of twin babies">
      <defs>
        <radialGradient id="scanTone" cx="0.5" cy="0.5" r="0.6">
          <stop offset="0" stop-color="#b86a55"/>
          <stop offset="0.6" stop-color="#8a3e30"/>
          <stop offset="1" stop-color="#3a1410"/>
        </radialGradient>
      </defs>
      <circle cx="165" cy="165" r="160" fill="url(#scanTone)" stroke="#d9ab4a" stroke-width="6"/>
    </svg>
  </section>
</main>
</body>
</html>
```